Poster design for - Silver Heron Gathering

To design a dynamic illustrated Silver Heron Gathering poster.
The dates are: 3-5 July 2020
Location: Fennick Meadow, Tarwick, Bedfordshire
www.silverheronmeet.co.uk

Here is some text about the event to give you an idea. You can take elements from it if you like:

A Gathering of Female Energy to Ignite and Embrace the Power of Woman with Mother Earth.

Target Market(s)

Women festival goers.

Industry/Entity Type

Festival

Colors

Designer to choose colors to be used in the design.

Requirements
Must have
• Silver Heron Logo - but this can be altered to look washed out.
• Date, location, website url.
Nice to have
• Earthy, hippy, festival look.

```html
<!DOCTYPE html>
<html lang="en">
<head>
<meta charset="utf-8">
<title>Silver Heron Gathering – 3-5 July 2020</title>
<link rel="stylesheet" href="https://fonts.googleapis.com/css2?family=Mulish:wght@300;600;700;800&family=Alegreya+Sans:wght@800&display=swap">
<style>
  :root {
    --ink: #070808;
    --paper: #ffffff;
    --ember: #f5301e;
  }
  * { margin: 0; padding: 0; box-sizing: border-box; }
  html, body { width: 848px; height: 1200px; overflow: hidden; background: var(--paper); }
  .poster {
    position: relative;
    width: 848px;
    height: 1200px;
    overflow: hidden;
    background: var(--paper);
    font-family: "Mulish", sans-serif;
  }
  .artwork-area {
    position: absolute;
    background: var(--ink);
  }
  .artwork-area--upper { left: 340px; top: 0; width: 508px; height: 1200px; }
  .artwork-area--lower { left: 0; top: 860px; width: 848px; height: 340px; }
  .frame {
    position: absolute;
    left: 52px; top: 65px;
    width: 742px; height: 1079px;
    border: 13px solid var(--ember);
  }
  .event-details {
    position: absolute;
    left: 80px; top: 462px;
    transform-origin: 0 0;
    transform: rotate(-90deg);
    color: var(--ink);
    white-space: nowrap;
  }
  .event-dates {
    font-weight: 700;
    font-size: 58px;
    line-height: 60px;
    letter-spacing: 1px;
  }
  .event-location {
    font-weight: 800;
    font-size: 26px;
    line-height: 44px;
    text-align: right;
    margin-top: 4px;
  }
  .brand {
    position: absolute;
    left: 400px; top: 104px;
    width: 260px;
    text-align: center;
    color: var(--ember);
    font-family: "Mulish", sans-serif;
    font-weight: 800;
  }
  .brand-mark {
    display: block;
    width: 60px; height: 60px;
    margin: 0 auto 20px;
    border-radius: 50%;
    background: var(--ember);
  }
  .brand-name {
    display: block;
    font-size: 32px;
    line-height: 40px;
    letter-spacing: 1px;
    text-transform: uppercase;
    white-space: nowrap;
  }
  .title {
    position: absolute;
    left: 456px; top: 568px;
    color: var(--paper);
    font-family: "Alegreya Sans", sans-serif;
    font-weight: 800;
    font-size: 80px;
    line-height: 72px;
  }
  .subtitle {
    position: absolute;
    left: 456px; top: 738px;
    color: var(--paper);
    font-family: "Mulish", sans-serif;
    font-weight: 300;
    font-size: 46px;
    line-height: 56px;
  }
  .invitation {
    position: absolute;
    right: 153px; top: 914px;
    width: 640px;
    text-align: right;
    color: var(--paper);
    font-weight: 600;
    font-size: 15.5px;
    line-height: 20.5px;
    white-space: nowrap;
  }
  .invitation strong { font-size: 19px; font-weight: 600; }
  .website {
    position: absolute;
    left: 0; width: 848px; top: 1060px;
    text-align: center;
    color: var(--paper);
    font-weight: 800;
    font-size: 27px;
    letter-spacing: 0.5px;
  }
</style>
</head>
<body>
<main class="poster">
  <div class="artwork-area artwork-area--upper" role="img" aria-label="Black ink-splash illustration of a woman with flowing hair"></div>
  <div class="artwork-area artwork-area--lower" role="img" aria-label="Lower part of the black ink-splash illustration"></div>

  <div class="frame"></div>

  <div class="event-details">
    <p class="event-dates">3-5 July 2020</p>
    <p class="event-location">Location: Fennick Meadow,<br>Tarwick, Bedfordshire</p>
  </div>

  <div class="brand">
    <span class="brand-mark"></span>
    <span class="brand-name">Silver Heron</span>
  </div>

  <h1 class="title">Silver<br>Heron</h1>
  <p class="subtitle">gathering</p>

  <p class="invitation">
    <strong>Join us</strong> - in the heart of the fire!<br>
    <strong>Join us</strong> - a gathering of incredible women from across this beautiful planet.<br>
    <strong>Join us</strong> - in our heart-space of laughter, knowledge, fun,<br>
    creativity, friendship, healing, growth and wildness, immersed in nature.
  </p>

  <p class="website">www.silverheronmeet.co.uk</p>
</main>
</body>
</html>
```